Mindfulness School for Children -- Business Cards

We're looking for business cards for our school directors and owners. We're a mindfulness school for children called little lanterns. Attached are our logos/icons.

```html
<!DOCTYPE html>
<html lang="en">
<head>
<meta charset="utf-8">
<title>little lanterns — business card</title>
<link rel="stylesheet" href="https://fonts.googleapis.com/css2?family=Crimson+Pro:wght@400;500&display=swap">
<style>
  :root {
    --page: #8e8e8e;
    --card: #ffffff;
    --teal: #4ba9c1;
    --teal-deep: #3d9fb9;
    --sage: #8fc992;
    --sage-text: #6fae8f;
    --ink: #555a5e;
    --faint: #eef6f8;
    --pattern-light: #47e6f7;
    --pattern-mid: #2aa2bc;
    --pattern-dark: #0f5e86;
  }
  * { box-sizing: border-box; margin: 0; padding: 0; }
  html, body { width: 1200px; height: 1200px; overflow: hidden; }
  body {
    position: relative;
    background: var(--page);
    font-family: "Crimson Pro", Georgia, serif;
  }
  .card {
    position: absolute;
    left: 262px;
    width: 686px;
    height: 392px;
    border-radius: 20px;
    overflow: hidden;
  }
  .card--front { top: 165px; background: var(--card); }
  .card--back { top: 653px; }

  .front__backdrop {
    position: absolute;
    left: 100px; top: 0;
    width: 486px; height: 377px;
    background: radial-gradient(ellipse at 50% 55%, var(--faint) 0%, rgba(238,246,248,0.5) 55%, rgba(255,255,255,0) 75%);
  }
  .brand-name {
    position: absolute;
    left: 0; right: 0;
    top: 118px;
    text-align: center;
    font-size: 48px;
    font-weight: 400;
    color: var(--teal);
    letter-spacing: 0.5px;
  }
  .person {
    position: absolute;
    right: 382px;
    top: 205px;
    text-align: right;
    color: var(--ink);
    font-size: 16px;
    line-height: 19px;
  }
  .person__name { font-size: 24px; line-height: 26px; color: var(--teal); }
  .person__role { font-size: 16px; line-height: 18px; color: var(--sage-text); margin-bottom: 5px; }
  .divider {
    position: absolute;
    left: 316px; top: 210px;
    width: 1px; height: 81px;
    background: var(--teal);
  }
  .contacts {
    position: absolute;
    left: 330px; top: 210px;
    list-style: none;
    color: var(--ink);
    font-size: 16px;
  }
  .contacts li { display: flex; align-items: center; height: 19.7px; }
  .contacts svg { width: 12px; height: 12px; margin-right: 10px; fill: var(--sage-text); }
  .band {
    position: absolute;
    left: 0; right: 0; bottom: 0;
    height: 15px;
  }

  .back__pattern {
    position: absolute; inset: 0;
    background: linear-gradient(110deg, var(--pattern-light) 0%, var(--pattern-mid) 45%, var(--pattern-dark) 100%);
  }
  .back__name {
    position: absolute;
    left: 520px; top: 312px;
    width: 140px;
    text-align: center;
    color: #ffffff;
    font-size: 22px;
    line-height: 24px;
  }
</style>
</head>
<body>
  <section class="card card--front">
    <div class="front__backdrop" role="img" aria-label="Faint large decorative brand emblem behind the card text"></div>
    <div class="brand-name">little lanterns</div>

    <div class="person">
      <div class="person__name">Daniel Hart</div>
      <div class="person__role">President</div>
      <div>4120 Willow Bend Road</div>
      <div>Juneau, Alaska 99801</div>
    </div>

    <div class="divider"></div>

    <ul class="contacts">
      <li><svg viewBox="0 0 12 12"><path d="M2.4 0.5l2 2.2-1 1.4c0.7 1.6 2 2.9 3.6 3.6l1.4-1 2.2 2-1.2 2C5 10.5 1.5 7 0.5 1.7z"/></svg>555-214-3087</li>
      <li><svg viewBox="0 0 12 12"><path d="M3 0h6v12H3zM4 1.5v8h4v-8z"/></svg>555-307-6192</li>
      <li><svg viewBox="0 0 12 12"><path d="M0 2.5h12v7H0zM1 3.5l5 3.5 5-3.5v-0.2H1z"/></svg>name@littlelanterns.com</li>
      <li><svg viewBox="0 0 12 12"><circle cx="6" cy="6" r="5.5"/></svg>littlelanterns.com</li>
    </ul>

    <svg class="band" viewBox="0 0 686 15" preserveAspectRatio="none" aria-hidden="true">
      <polygon points="0,0 338,0 334,15 0,15" fill="var(--sage)"/>
      <polygon points="342,0 686,0 686,15 338,15" fill="var(--teal-deep)"/>
    </svg>
  </section>

  <section class="card card--back">
    <div class="back__pattern" role="img" aria-label="Repeating decorative emblem pattern shading from bright aqua to deep teal"></div>
    <div class="back__name">little lanterns</div>
  </section>
</body>
</html>
```